Corvane Freight Company Business Card Design

We are a company that delivers natural saltwater (from the ocean) to aquarium companies, restaurants and home marine tanks. I would like a new business card to suit.

Must include Name, company name, abn, contact number and website as well as logo (see attached).

Looking for a design that stands out, has a clean but unique appearance.

Double and single sided entries welcome

Business

• Logo

```html
<!DOCTYPE html>
<html lang="en">
<head>
<meta charset="utf-8">
<title>Corvane Freight Company – Business Card</title>
<link rel="stylesheet" href="https://fonts.googleapis.com/css2?family=Source+Sans+3:wght@400;600;700&display=swap">
<style>
  :root {
    --backdrop: #1c1c1e;
    --front-blue: #1c68ea;
    --wave-light: #4db4ef;
    --wave-line: #e8f6ff;
    --back-blue: #3fb2f2;
    --white: #ffffff;
    --soft-white: #eaf4ff;
  }
  * { margin: 0; padding: 0; box-sizing: border-box; }
  html, body {
    width: 1200px; height: 1032px; overflow: hidden;
    background: var(--backdrop);
    font-family: "Source Sans 3", "Myriad Pro", Arial, sans-serif;
  }
  .canvas { position: relative; width: 1200px; height: 1032px; }

  .card {
    position: absolute;
    width: 743px; height: 424px;
    border-radius: 20px;
    overflow: hidden;
  }
  .card--front { left: 68px; top: 62px; background: var(--front-blue); }
  .card--back  { left: 371px; top: 538px; background: var(--back-blue); }

  .wordmark {
    position: absolute; left: 0; right: 0;
    display: flex; align-items: center; justify-content: center; gap: 14px;
    color: var(--white);
    font-weight: 700; font-size: 44px; letter-spacing: -0.5px;
  }
  .wordmark__dot {
    width: 20px; height: 20px; border-radius: 50%;
    background: var(--white);
  }
  .card--front .wordmark { top: 78px; }
  .card--back .wordmark { top: 160px; }

  .contact {
    position: absolute; top: 226px;
    color: var(--soft-white);
    font-size: 17px; line-height: 25px;
  }
  .contact--address { right: 392px; text-align: right; }
  .contact--address .contact__company { font-size: 19px; }
  .contact--details { left: 389px; }
  .contact__divider {
    position: absolute; left: 371px; top: 228px;
    width: 1.5px; height: 78px; background: var(--soft-white);
  }
  .contact__row { display: flex; align-items: center; gap: 6px; }
  .contact__row svg { width: 14px; height: 14px; flex: none; }

  .card__wave { position: absolute; inset: 0; width: 100%; height: 100%; }

  .holder {
    position: absolute; left: 55px; top: 376px;
    color: var(--white); font-size: 24px;
  }
  .holder__name { font-weight: 700; }
  .holder__title { font-weight: 400; font-size: 21px; }

  .back__website {
    position: absolute; left: 0; right: 0; top: 338px;
    text-align: center; color: var(--white);
    font-size: 21px; letter-spacing: 3.5px;
  }
</style>
</head>
<body>
<main class="canvas">

  <section class="card card--front" aria-label="Business card front">
    <svg class="card__wave" viewBox="0 0 743 424" preserveAspectRatio="none" aria-hidden="true">
      <path d="M0 332 C190 312 360 362 520 398 C610 416 690 392 743 352 L743 424 L0 424 Z" fill="var(--wave-light)"/>
      <path d="M0 332 C190 312 360 362 520 398 C610 416 690 392 743 352" fill="none" stroke="var(--wave-line)" stroke-width="4"/>
      <path d="M0 350 C200 336 370 384 530 412 C610 426 690 410 743 380" fill="none" stroke="var(--front-blue)" stroke-width="3" opacity="0.55"/>
    </svg>

    <div class="wordmark"><span class="wordmark__dot"></span>Corvane Freight Company</div>

    <div class="contact contact--address">
      <div class="contact__company">Corvane Freight Company</div>
      <div>Street Name, City Name</div>
      <div>State, City Zip Code</div>
    </div>
    <div class="contact__divider"></div>
    <div class="contact contact--details">
      <div class="contact__row">
        <svg viewBox="0 0 14 14" aria-hidden="true"><circle cx="7" cy="7" r="6.3" fill="none" stroke="#fff" stroke-width="1.2"/><path d="M4.5 3.8 L6 3.5 L6.6 5.4 L5.7 6 C6.1 7 7 7.9 8 8.3 L8.6 7.4 L10.5 8 L10.2 9.5 C7.2 9.8 4.2 6.8 4.5 3.8 Z" fill="#fff"/></svg>
        <span>123-456-7890</span>
      </div>
      <div class="contact__row">
        <svg viewBox="0 0 14 14" aria-hidden="true"><circle cx="7" cy="7" r="6" fill="#fff"/><path d="M1 7 H13 M7 1 C4 4 4 10 7 13 M7 1 C10 4 10 10 7 13" fill="none" stroke="var(--front-blue)" stroke-width="1"/></svg>
        <span>www.website.com</span>
      </div>
      <div>ABN : 0123456789</div>
    </div>

    <div class="holder"><span class="holder__name">Your name,</span> <span class="holder__title">Title</span></div>
  </section>

  <section class="card card--back" aria-label="Business card back">
    <div class="wordmark"><span class="wordmark__dot"></span>Corvane Freight Company</div>
    <div class="back__website">www.website.com</div>
  </section>

</main>
</body>
</html>
```